Business Card - connecting 2 souls and beggining the journey of self discovery

Logo on the front
with tag line

On the back list of services and contact details

Seminars
workshops
Coaching
podcasts

Darren Whitlow
Health & Wellbeing Life Coach
0491 372 615
darren@brightcoreliving.example
brightcoreliving.example

Industry/Entity Type

Life Coaching

Contact Information for Business Card

I like the use of colour from the logo to be used. I'm not a fan of white.

Requirements
Must have
• My tagline: The journey home starts with you
Nice to have
• Use of colour that is in the Brightcore Living logo

```html
<!DOCTYPE html>
<html lang="en">
<head>
<meta charset="utf-8">
<title>Darren Whitlow – Business Card</title>
<link rel="stylesheet" href="https://fonts.googleapis.com/css2?family=Quicksand:wght@400;500;600;700&display=swap">
<style>
  :root {
    --canvas: #141414;
    --card: #ffffff;
    --green: #7cbc1e;
    --green-dark: #6aa516;
    --charcoal: #3b3b3d;
    --ink: #2d2d2f;
    --white: #ffffff;
    --mark: #f08a24;
  }
  html, body {
    margin: 0;
    width: 1200px;
    height: 1200px;
    overflow: hidden;
    background: var(--canvas);
    font-family: "Quicksand", sans-serif;
  }
  .sheet {
    width: 1200px;
    height: 1200px;
    display: flex;
    flex-direction: column;
    align-items: center;
    justify-content: space-evenly;
  }
  .card {
    width: 900px;
    height: 514px;
    display: block;
    background: var(--card);
  }
  .brand-name { font-weight: 700; fill: var(--green-dark); }
  .tagline { font-weight: 600; fill: var(--ink); }
  .holder-first { font-weight: 700; fill: var(--green); }
  .holder-last { font-weight: 700; fill: var(--ink); }
  .holder-role { font-weight: 400; fill: var(--ink); }
  .contact-text, .service-text { font-weight: 600; fill: var(--white); }
  .band-green { fill: var(--green); }
  .band-dark { fill: var(--charcoal); }
  .icon-disc { fill: var(--white); }
  .icon-line { fill: none; stroke: var(--green); stroke-width: 2.2; stroke-linecap: round; stroke-linejoin: round; }
  .brand-disc { fill: var(--mark); }
</style>
</head>
<body>
<main class="sheet">

  <!-- Contact side -->
  <svg class="card card-contact" viewBox="0 0 900 514" role="img" aria-label="Contact side of the business card for Darren Whitlow">
    <text x="51" y="123" font-size="41"><tspan class="holder-first">Darren</tspan><tspan class="holder-last"> Whitlow</tspan></text>
    <text class="holder-role" x="51" y="155" font-size="22">Health &amp; Wellbeing Life Coach</text>

    <g class="brand-lockup">
      <circle class="brand-disc" cx="722" cy="100" r="62"/>
      <text class="brand-name" x="722" y="190" font-size="20" text-anchor="middle">Brightcore Living</text>
      <text class="tagline" x="712" y="238" font-size="21" text-anchor="middle">The journey home starts with you</text>
    </g>

    <path class="band-dark" d="M300 340 Q312 321 340 321 L900 321 L900 345 L300 345 Z"/>
    <path class="band-green" d="M258 340 L900 340 L900 514 L121 514 L215 362 Q228 340 258 340 Z"/>
    <path class="band-green" d="M0 399 L100 399 Q125 399 117 420 L80 514 L0 514 Z"/>

    <g class="contact-list">
      <circle class="icon-disc" cx="252" cy="381" r="17"/>
      <path class="icon-line" d="M245 372 q-3 3 0 9 q4 8 12 11 q5 2 7 -2 l-4 -4 q-2 2 -4 1 q-4 -3 -6 -7 q0 -2 2 -3 l-3 -5 z"/>
      <text class="contact-text" x="290" y="389" font-size="21">0491 372 615</text>

      <circle class="icon-disc" cx="228" cy="434" r="17"/>
      <circle class="icon-line" cx="228" cy="434" r="9"/>
      <path class="icon-line" d="M219 434 h18 M228 425 q-6 9 0 18 M228 425 q6 9 0 18"/>
      <text class="contact-text" x="262" y="442" font-size="20">www.brightcoreliving.example</text>

      <circle class="icon-disc" cx="197" cy="487" r="17"/>
      <rect class="icon-line" x="188" y="481" width="18" height="12" rx="1"/>
      <path class="icon-line" d="M188 481 l9 7 l9 -7"/>
      <text class="contact-text" x="231" y="495" font-size="20">darren@brightcoreliving.example</text>
    </g>

    <line x1="567" y1="400" x2="567" y2="500" stroke="#ffffff" stroke-opacity="0.35" stroke-width="1.5"/>

    <g class="service-list">
      <circle cx="604" cy="402" r="3.5" fill="#fff"/>
      <text class="service-text" x="617" y="409" font-size="21">Seminars</text>
      <circle cx="604" cy="444" r="3.5" fill="#fff"/>
      <text class="service-text" x="617" y="451" font-size="21">Workshops</text>
      <circle cx="771" cy="402" r="3.5" fill="#fff"/>
      <text class="service-text" x="784" y="409" font-size="21">Coaching</text>
      <circle cx="771" cy="444" r="3.5" fill="#fff"/>
      <text class="service-text" x="784" y="451" font-size="21">Podcasts</text>
    </g>
  </svg>

  <!-- Brand side -->
  <svg class="card card-brand" viewBox="0 0 900 514" role="img" aria-label="Brand side of the business card with tagline">
    <path class="band-green" d="M0 198 L90 198 Q118 198 114 222 L72 316 L0 316 Z"/>
    <path class="band-green" d="M900 198 L810 198 Q782 198 786 222 L828 316 L900 316 Z"/>

    <g class="brand-lockup">
      <circle class="brand-disc" cx="450" cy="178" r="100"/>
      <text class="brand-name" x="450" y="318" font-size="26" text-anchor="middle">Brightcore Living</text>
      <text class="tagline" x="450" y="372" font-size="32" text-anchor="middle">The journey home starts with you</text>
    </g>
  </svg>

</main>
</body>
</html>
```